Online Shop Maren

We need a web design for an online shop, called "Lirvo Dune Jewels". The shop should have an extraordinary, elegant look, as shown in the Quellwick Advertising Picture in our Briefing.pdf (attached). Please have a look at our Briefing regarding website colours, background ideas, and elements to be included. The online shop is about professional jewellery design pieces, where each piece is handmade of high quality materials, also unique pieces and unique editions possible. It should attract extraordinary people and visualize that its a very individual and unique design jewellery. You can get an idea of whom it should attract by reading our target group. Colours to be used are jewellery-Velvet red, Black / anthracite, exclusive colours, silverish-white, bronze-brown and golden.

Please play around when designing with the image pictures we attach, preferably more vertical pictures, no panoramic pictures like in Brovenka Shop. Also include the BLACK logo of lirvo dune. We include the SITEMAP in the briefing and also another folder with product pictures you can use for the draft.

Regarding Functions, the store will have the SAME (technical) functions as this page:http://www.brovenka-shop.eu/ - using the "most famous" products/categories for the starting page, going into individual product pages by clicking these images and then leading to a detailed page for one product only.

Target Market(s)

Jewellery-lovers, who appreciate extraordinary things, creative economy/fashion-industries, stylists, Style consultants, outfitter, theatres, operas, production sites, Cocktail-, Dinner and Bridefashion, exclusive traditional costume stores, dancesports and tango argento dancers

Industry/Entity Type

Shop

Requirements
Must have
• Must include:
• Colours as per briefing
• Background ideas/images as per briefing/pictures sent
• Sitemap as per briefing
• Social buttons
• Logo
• Design for 3 pages: Starting page showing big images, attractive design and the 4 popular categories
• Subpage with different products of one category (i.e. bracelets)
• Detail page with one individual product only
Should not have
• no fresh, playful colours like yellow, orange, green, blue
• no cheap design, no panorama pictures

```html
<!DOCTYPE html>
<html lang="de">
<head>
<meta charset="utf-8">
<title>Lirvo Dune Jewels – Online Shop</title>
<link rel="stylesheet" href="https://fonts.googleapis.com/css2?family=Arimo:wght@400;700&family=Open+Sans:wght@400&family=Dancing+Script:wght@600&family=Merriweather:wght@300;400&display=swap">
<style>
:root{
  --wood-dark:#240c05;
  --wood-mid:#4a1c0d;
  --wood-light:#64291a;
  --panel-black:#141414;
  --panel-line:#2a2a2a;
  --nav-text:#c4c4c4;
  --accent-red:#e0121b;
  --paper:#e1e1e1;
  --paper-dark:#d2d2d2;
  --card-wood:#ecc98e;
  --card-wood-light:#f6e0b6;
  --btn-brown:#4a140a;
  --text-dark:#1e1e1e;
  --white:#ffffff;
  --pay-blue:#1f4d8a;
}
*{margin:0;padding:0;box-sizing:border-box}
html,body{width:817px;height:1200px;overflow:hidden}
body{
  position:relative;
  font-family:"Arimo",Arial,sans-serif;
  background:
    repeating-linear-gradient(92deg,rgba(0,0,0,.08) 0 3px,transparent 3px 9px,rgba(255,255,255,.03) 9px 11px,transparent 11px 17px),
    linear-gradient(90deg,var(--wood-dark) 0%,var(--wood-light) 22%,var(--wood-mid) 50%,var(--wood-light) 78%,var(--wood-dark) 100%);
}
.abs{position:absolute}

/* top bar */
.topbar{left:69px;top:0;width:680px;height:27px;background:linear-gradient(180deg,#232323,#161616);color:var(--nav-text);font-size:9px;display:flex;align-items:center;padding:0 18px}
.topbar .cart{display:flex;align-items:center;gap:7px;color:#8a8a8a}
.topbar .contact{margin-left:auto;display:flex;gap:20px;color:#d6d6d6}
.topbar .contact span{display:flex;align-items:center;gap:4px}

/* logo */
.logo{left:69px;top:27px;width:213px;height:104px;background:linear-gradient(180deg,#5a5a5a 0%,#3a3a3a 55%,#1e1e1e 100%);text-align:center}
.logo .name{font-family:"Open Sans",sans-serif;font-size:31px;padding-top:15px;color:#1a1a1a;letter-spacing:.3px;line-height:36px}
.logo .sub{font-family:"Open Sans",sans-serif;font-size:17px;color:#1a1a1a;line-height:24px}

/* side navigation */
.sidenav{left:69px;top:131px;width:213px;height:304px;background:linear-gradient(180deg,#1a1a1a,#0f0f0f)}
.sidenav ul{list-style:none}
.sidenav li{height:33px;border-bottom:1px solid var(--panel-line);box-shadow:0 1px 0 #000;display:flex;align-items:center;padding:0 19px;font-size:11px;color:var(--nav-text)}
.sidenav li.active{color:var(--accent-red)}
.sidenav li svg{margin-left:auto}
.touch{padding:30px 19px 0;font-size:11px;color:var(--nav-text)}
.touch .icons{display:flex;gap:4px;margin-top:9px}
.touch .icons span{width:18px;height:18px;border-radius:50%;background:radial-gradient(circle at 40% 35%,#9a9a9a,#5c5c5c);border:1px solid #3a3a3a}
.touch .like{width:27px;height:12px;background:#eceef4;border:1px solid #b8bccb;margin-top:6px;border-radius:2px}

/* hero */
.hero{left:283px;top:27px;width:466px;height:408px;
  background:
    radial-gradient(ellipse 95px 180px at 64% 62%,rgba(214,28,58,.95),rgba(214,28,58,.55) 55%,transparent 100%),
    radial-gradient(ellipse 60px 55px at 57% 23%,rgba(205,150,125,.8),transparent 100%),
    radial-gradient(ellipse 190px 230px at 20% 40%,rgba(58,40,70,.9),transparent 100%),
    linear-gradient(90deg,#2e2436 0%,#4c4256 30%,#6e6250 60%,#8c8770 85%,#6e6b58 100%);}
.dots{left:487px;top:414px;display:flex;gap:3px}
.dots i{width:9px;height:9px;border-radius:50%;background:#000}
.dots i.on{background:#fff}

/* tagline */
.tagline{left:69px;top:435px;width:680px;height:91px;background:linear-gradient(180deg,#0d0d0d,#181818);border-bottom:3px dashed #4a4a4a;color:#9a9a9a;font-family:"Merriweather",serif;font-weight:300;font-size:10.5px;text-align:center;line-height:17px;padding-top:20px}

/* content */
.content{left:69px;top:526px;width:680px;height:626px;background:linear-gradient(180deg,var(--paper),var(--paper-dark))}
.cat-head{left:87px;top:561px;width:144px;height:30px;background:linear-gradient(180deg,#5a1a0e,#3a0f07);color:var(--white);font-family:"Dancing Script",cursive;font-size:17px;display:flex;align-items:center;padding-left:12px}
.cat-list{left:87px;top:591px;width:144px;background:var(--white);list-style:none;border:1px solid #cfcfcf;border-top:none}
.cat-list li{height:23px;border-bottom:1px dashed #cfcfcf;font-size:10.5px;color:var(--text-dark);display:flex;align-items:center;padding-left:11px}
.cat-list li:last-child{border-bottom:none}
.promo{left:87px;top:700px;width:144px;height:222px;
  background:
    radial-gradient(ellipse 55px 40px at 60% 62%,rgba(255,255,255,.95),transparent 100%),
    radial-gradient(ellipse 40px 90px at 30% 55%,rgba(40,24,26,.85),transparent 100%),
    radial-gradient(ellipse 35px 30px at 55% 22%,rgba(210,170,150,.9),transparent 100%),
    linear-gradient(180deg,#d9d4d2 0%,#c2b6b2 45%,#ece9e8 100%);}
.promo .caption{position:absolute;left:33px;top:157px;font-family:"Dancing Script",cursive;font-size:16px;color:#111;line-height:17px}
.promo .cta{position:absolute;right:6px;bottom:7px;background:#111;color:#fff;font-size:9px;padding:2px 5px;font-weight:700}
.pay-label{left:87px;top:942px;font-size:10.5px;color:var(--text-dark)}
.pay-name{left:87px;top:961px;font-size:17px;font-weight:700;color:var(--pay-blue)}

.main-head{left:250px;top:553px;font-family:"Dancing Script",cursive;font-weight:600;font-size:25px;color:#1d1d1d}
.grid{left:250px;top:602px;display:grid;grid-template-columns:repeat(3,152px);grid-template-rows:repeat(2,259px);column-gap:12px;row-gap:12px}
.card{background:
    repeating-linear-gradient(90deg,rgba(180,130,60,.12) 0 2px,transparent 2px 7px),
    linear-gradient(90deg,var(--card-wood),var(--card-wood-light),var(--card-wood));
  padding:7px;border:1px solid #d2a968}
.card .photo{height:174px;border:1px solid #8a6a3a}
.card .price{font-size:14px;color:var(--text-dark);margin-top:5px}
.card .desc{font-size:8.5px;color:var(--text-dark);margin-top:2px}
.card .actions{display:flex;align-items:center;justify-content:space-between;margin-top:11px}
.card .btn{width:102px;height:25px;background:linear-gradient(180deg,#5a1a0e,#3a0f07);color:#fff;font-family:"Merriweather",serif;font-weight:300;font-size:12px;display:flex;align-items:center;justify-content:center;border-radius:2px}
.p1{background:
    radial-gradient(ellipse 22px 30px at 30% 75%,#c9a23a,transparent 100%),
    radial-gradient(ellipse 22px 30px at 70% 75%,#c9a23a,transparent 100%),
    radial-gradient(ellipse 14px 28px at 30% 40%,#eeeae0,transparent 100%),
    radial-gradient(ellipse 14px 28px at 70% 40%,#eeeae0,transparent 100%),
    linear-gradient(180deg,#3c3c42,#2a2a2e);}
.p2{background:
    radial-gradient(ellipse 40px 80px at 50% 50%,#d8ae3c,#9a7424 60%,transparent 100%),
    linear-gradient(180deg,#1a1a1a,#262626);}
.p3{background:
    radial-gradient(ellipse 24px 34px at 50% 38%,#a89c86,transparent 100%),
    radial-gradient(ellipse 14px 40px at 50% 78%,#6e6656,transparent 100%),
    linear-gradient(180deg,#1e1e1e,#111);}
.p4{background:
    radial-gradient(ellipse 45px 35px at 40% 55%,#cfcfcf,transparent 100%),
    radial-gradient(ellipse 25px 30px at 72% 25%,#5c5c5c,transparent 100%),
    linear-gradient(180deg,#e4e4e4 0%,#8a8a8a 35%,#1e1e1e 70%,#3a2622 100%);}
.p5{background:
    radial-gradient(ellipse 55px 40px at 50% 45%,#c8c4cc,#7a7680 50%,transparent 100%),
    linear-gradient(180deg,#111,#0a0a0a);}
.p6{background:
    radial-gradient(circle at 50% 58%,#3a3a3a 0,#6a6a6a 20%,#2a2a2a 35%,transparent 50%),
    radial-gradient(ellipse 8px 60px at 42% 20%,#3a3a3a,transparent 100%),
    linear-gradient(180deg,#1e1e1e,#141414);}

/* footer */
.footer{left:69px;top:1170px;width:680px;display:flex;font-size:8px;color:#c7b4aa}
.footer nav{display:flex;gap:15px}
.footer nav .active{color:var(--accent-red)}
.footer .copy{margin-left:auto;color:#e8e0dc}
</style>
</head>
<body>

<header class="abs topbar">
  <div class="cart">
    <svg width="14" height="12" viewBox="0 0 14 12"><path d="M0 1h3l2 7h7l2-5H4" fill="none" stroke="#8a8a8a" stroke-width="1.3"/><circle cx="6" cy="10.5" r="1.2" fill="#8a8a8a"/><circle cx="11" cy="10.5" r="1.2" fill="#8a8a8a"/></svg>
    00 Produkt(e) im Warenkorb
  </div>
  <div class="contact">
    <span><svg width="8" height="7"><rect width="8" height="7" rx="1" fill="#ccc"/></svg>+ 43 (0) 660 48205173</span>
    <span><svg width="9" height="7"><rect width="9" height="7" fill="#ccc"/><path d="M0 0l4.5 4L9 0" stroke="#333" fill="none"/></svg>atelier@maren-atelier.net</span>
  </div>
</header>

<div class="abs logo">
  <div class="name">Lirvo Dune</div>
  <div class="sub">Jewels</div>
</div>

<nav class="abs sidenav">
  <ul>
    <li class="active">HOME</li>
    <li>Online Shop<svg width="12" height="12"><circle cx="6" cy="6" r="5" fill="none" stroke="#ccc" stroke-width="1.3"/><path d="M5 3.5L8 6L5 8.5Z" fill="#ccc"/></svg></li>
    <li>Info &amp; Facts<svg width="12" height="12"><circle cx="6" cy="6" r="5" fill="none" stroke="#ccc" stroke-width="1.3"/><path d="M5 3.5L8 6L5 8.5Z" fill="#ccc"/></svg></li>
    <li>Partner<svg width="12" height="12"><circle cx="6" cy="6" r="5" fill="none" stroke="#ccc" stroke-width="1.3"/><path d="M5 3.5L8 6L5 8.5Z" fill="#ccc"/></svg></li>
    <li>About me</li>
    <li>Contact</li>
  </ul>
  <div class="touch">
    Get in Touch :
    <div class="icons"><span></span><span></span><span></span></div>
    <div class="like"></div>
  </div>
</nav>

<div class="abs hero" role="img" aria-label="Model in a red silk dress wearing a gold bracelet and earrings"></div>
<div class="abs dots"><i></i><i class="on"></i><i></i><i></i><i></i></div>

<section class="abs tagline">
  <p>... außergewöhnliches Schmuckdesign für außergewöhnliche Menschen ...</p>
  <p>... Unikate und Editionen von Hand gefertigt ...</p>
  <p>... für alle Anlässe, für Bühne, Tanzsport und Red Carpet ...</p>
</section>

<main class="abs content"></main>

<div class="abs cat-head">Our Products:</div>
<ul class="abs cat-list">
  <li>Collier</li><li>Bracelet</li><li>Ring</li><li>Earring</li>
</ul>
<div class="abs promo" role="img" aria-label="Model in a white dress wearing a silver necklace">
  <div class="caption">Pellentesque<br>habitant</div>
  <div class="cta">Click Here</div>
</div>
<div class="abs pay-label">Bezahlen Sie bei uns mit:</div>
<div class="abs pay-name">Payvora</div>

<h2 class="abs main-head">Most Popular Products:</h2>
<section class="abs grid">
  <article class="card"><div class="photo p1" role="img" aria-label="Pearl and gold wire earrings"></div><div class="price">€ 00,00</div><div class="desc">Lorem ipsum dolor sit amet</div><div class="actions"><svg width="24" height="20" viewBox="0 0 24 20"><path d="M0 2h4l3 11h12l3-8H6" fill="none" stroke="#111" stroke-width="2.5"/><circle cx="9" cy="17" r="2" fill="#111"/><circle cx="17" cy="17" r="2" fill="#111"/></svg><span class="btn">Product Info</span></div></article>
  <article class="card"><div class="photo p2" role="img" aria-label="Gold wire mesh bracelet"></div><div class="price">€ 00,00</div><div class="desc">Lorem ipsum dolor sit amet</div><div class="actions"><svg width="24" height="20" viewBox="0 0 24 20"><path d="M0 2h4l3 11h12l3-8H6" fill="none" stroke="#111" stroke-width="2.5"/><circle cx="9" cy="17" r="2" fill="#111"/><circle cx="17" cy="17" r="2" fill="#111"/></svg><span class="btn">Product Info</span></div></article>
  <article class="card"><div class="photo p3" role="img" aria-label="Beaded pendant with tassel"></div><div class="price">€ 00,00</div><div class="desc">Lorem ipsum dolor sit amet</div><div class="actions"><svg width="24" height="20" viewBox="0 0 24 20"><path d="M0 2h4l3 11h12l3-8H6" fill="none" stroke="#111" stroke-width="2.5"/><circle cx="9" cy="17" r="2" fill="#111"/><circle cx="17" cy="17" r="2" fill="#111"/></svg><span class="btn">Product Info</span></div></article>
  <article class="card"><div class="photo p4" role="img" aria-label="Silver collars on display busts"></div><div class="price">€ 00,00</div><div class="desc">Lorem ipsum dolor sit amet</div><div class="actions"><svg width="24" height="20" viewBox="0 0 24 20"><path d="M0 2h4l3 11h12l3-8H6" fill="none" stroke="#111" stroke-width="2.5"/><circle cx="9" cy="17" r="2" fill="#111"/><circle cx="17" cy="17" r="2" fill="#111"/></svg><span class="btn">Product Info</span></div></article>
  <article class="card"><div class="photo p5" role="img" aria-label="Silver collier with crystal stones"></div><div class="price">€ 00,00</div><div class="desc">Lorem ipsum dolor sit amet</div><div class="actions"><svg width="24" height="20" viewBox="0 0 24 20"><path d="M0 2h4l3 11h12l3-8H6" fill="none" stroke="#111" stroke-width="2.5"/><circle cx="9" cy="17" r="2" fill="#111"/><circle cx="17" cy="17" r="2" fill="#111"/></svg><span class="btn">Product Info</span></div></article>
  <article class="card"><div class="photo p6" role="img" aria-label="Black beaded round pendant necklace"></div><div class="price">€ 00,00</div><div class="desc">Lorem ipsum dolor sit amet</div><div class="actions"><svg width="24" height="20" viewBox="0 0 24 20"><path d="M0 2h4l3 11h12l3-8H6" fill="none" stroke="#111" stroke-width="2.5"/><circle cx="9" cy="17" r="2" fill="#111"/><circle cx="17" cy="17" r="2" fill="#111"/></svg><span class="btn">Product Info</span></div></article>
</section>

<footer class="abs footer">
  <nav><span class="active">HOME</span><span>Online Shop</span><span>Info &amp; Facts</span><span>Partner</span><span>About me</span><span>Contact</span></nav>
  <span class="copy">© 2013 Lirvo Dune Jewels . All rights reserved.</span>
</footer>

</body>
</html>
```